Transport & Storage Company needs a revamp of current card

Would like to keep same colours & basic design but would like to "sharpen" up look of card.

Please remove "The Brisk Haulers"

Please add 1800 418 239 on front & back of card

Please add email address on back of card - colin@bluegatefreight.com.au

I would like our ABN No - 38 214 906 731 on back of card (which currently has logo only). Logo on back of card can be removed if insufficient space.

Please design another card (same as above) but with Maren Ashcombe - 0431 702 548, maren@bluegatefreight.com.au

I do not want cards to look "too busy" so please re-arrange layout of card if necessary.

Target Market(s)

Transport & Storage

Industry/Entity Type

It Company

Contact Information for Business Card

Please refer to attached current business card

Font styles to use
Other font styles liked:
• Tahoma

Requirements
Must have
• Refer to project decsription
Nice to have
Should not have

```html
<!DOCTYPE html>
<html lang="en">
<head>
<meta charset="utf-8">
<title>Bluegate Freight – Business Cards</title>
<link rel="stylesheet" href="https://fonts.googleapis.com/css2?family=Open+Sans:wght@400;600;700&display=swap">
<style>
  :root {
    --backdrop: #cbb09a;
    --card: #ffffff;
    --purple: #743a84;
    --charcoal: #58585a;
  }
  * { margin: 0; padding: 0; box-sizing: border-box; }
  html, body {
    width: 1200px; height: 1200px; overflow: hidden;
    background: var(--backdrop);
    font-family: "Open Sans", Tahoma, sans-serif;
  }
  .card {
    position: absolute; left: 117px;
    width: 936px; height: 548px;
    background: var(--card);
    overflow: hidden;
    color: var(--purple);
  }
  .card--front { top: 35px; }
  .card--back { top: 619px; }
  .bands { position: absolute; inset: 0; width: 100%; height: 100%; }
  .bands .band-grey { fill: var(--charcoal); }
  .bands .band-purple { fill: var(--purple); }

  .brand-name {
    position: absolute;
    font-weight: 700;
    color: var(--purple);
    white-space: nowrap;
    letter-spacing: -0.5px;
  }
  .card--front .brand-name { left: 63px; top: 110px; font-size: 52px; }
  .card--back .brand-name { left: 0; right: 0; top: 120px; text-align: center; font-size: 72px; }

  .contact { position: absolute; line-height: 1; }
  .card--front .contact { left: 519px; top: 250px; font-size: 24px; }
  .contact .person { font-weight: 700; font-size: 29px; margin-bottom: 10px; }
  .contact .line { margin-bottom: 10px; }
  .contact .web { margin-top: 38px; font-size: 23px; }

  .card--back .contact {
    left: 0; right: 0; top: 299px;
    text-align: center; font-size: 26px;
  }
  .card--back .contact .line { margin-bottom: 8px; }
</style>
</head>
<body>

<section class="card card--front">
  <svg class="bands" viewBox="0 0 936 548" preserveAspectRatio="none" aria-hidden="true">
    <polygon class="band-grey" points="0,368 936,515 936,522 0,442"/>
    <polygon class="band-purple" points="0,464 936,527 936,548 0,548"/>
  </svg>
  <div class="brand-name">Bluegate Freight</div>
  <div class="contact">
    <p class="person">Colin Tresham</p>
    <p class="line">0452 317 806</p>
    <p class="line">1800 418 239</p>
    <p class="web">www.bluegatefreight.com.au</p>
  </div>
</section>

<section class="card card--back">
  <svg class="bands" viewBox="0 0 936 548" preserveAspectRatio="none" aria-hidden="true">
    <polygon class="band-grey" points="0,368 936,515 936,522 0,442"/>
    <polygon class="band-purple" points="0,464 936,527 936,548 0,548"/>
  </svg>
  <div class="brand-name">Bluegate Freight</div>
  <div class="contact">
    <p class="line">ABN No - 38 214 906 731</p>
    <p class="line">1800 418 239</p>
    <p class="line">colin@bluegatefreight.com.au</p>
  </div>
</section>

</body>
</html>
```